Business Card and Letterhead for Pimlu - modern real estate business

I need a double sided business card design for Pimlu. Please see business card brief here https://files.trelvonadocs.com/sheet/r/7QzTmWbaXLJnoPEd-kRyUgFhHsstbvCe2qfoMxDa_pz/view?mode=shared

Please feel free to design the business cards however you feel best. I am happy to give some creative freedoms and then provide feedback from there.

Please then also create a letterhead to match the business card design

Colors

Designer to choose colors to be used in the design.

Requirements
Must have
• Must be a modern, elegant business card which looks very professional

```html
<!DOCTYPE html>
<html lang="en">
<head>
<meta charset="utf-8">
<title>Pimlu Business Card</title>
<link href="https://fonts.googleapis.com/css2?family=Roboto:wght@400;500;700&display=swap" rel="stylesheet">
<style>
  :root {
    --brand-red: #e30613;
    --ink-dark: #2a2a2a;
    --ink-body: #555555;
    --ink-title: #333333;
    --card-white: #ffffff;
    --canvas-bg: #ececec;
    --photo-top: #b9c4c9;
    --photo-bottom: #4a4f4c;
  }
  * { box-sizing: border-box; margin: 0; padding: 0; }
  html, body {
    width: 1125px;
    height: 1200px;
    overflow: hidden;
    background: var(--canvas-bg);
    font-family: "Roboto", Arial, sans-serif;
  }
  .card {
    position: absolute;
    left: 162px;
    width: 800px;
    height: 457px;
    box-shadow: 0 3px 10px rgba(0,0,0,0.18);
  }
  .card-front { top: 104px; background: var(--card-white); }
  .card-back { top: 638px; background: var(--ink-dark); }

  .wordmark {
    font-family: "Roboto", Arial, sans-serif;
    font-weight: 700;
    color: var(--brand-red);
    letter-spacing: 2px;
    line-height: 1;
  }
  .card-front .wordmark {
    position: absolute;
    left: 74px;
    top: 104px;
    font-size: 74px;
  }
  .address {
    position: absolute;
    left: 76px;
    top: 218px;
    font-size: 18px;
    line-height: 22px;
    color: var(--ink-body);
  }
  .contact-list {
    position: absolute;
    left: 76px;
    top: 282px;
    list-style: none;
    font-size: 18px;
    line-height: 22.5px;
    color: var(--ink-body);
  }
  .contact-list li { display: flex; align-items: center; }
  .contact-list svg { width: 14px; height: 14px; margin-right: 11px; fill: var(--brand-red); }

  .portrait {
    position: absolute;
    left: 555px;
    top: 81px;
    width: 159px;
    height: 181px;
    border: 1px solid #222;
    background: linear-gradient(180deg, var(--photo-top) 0%, #8d8a7e 45%, var(--photo-bottom) 100%);
  }
  .agent {
    position: absolute;
    right: 86px;
    top: 295px;
    text-align: right;
  }
  .agent-name {
    font-size: 26px;
    font-weight: 700;
    color: var(--brand-red);
    line-height: 32px;
  }
  .agent-title {
    font-size: 18px;
    font-weight: 500;
    color: var(--ink-title);
    line-height: 24px;
  }
  .rule-thin {
    position: absolute;
    left: 0; right: 0;
    top: 431px;
    height: 2px;
    background: var(--ink-dark);
  }
  .rule-band {
    position: absolute;
    left: 0; right: 0;
    top: 436px;
    height: 21px;
    background: var(--brand-red);
  }
  .card-back .wordmark {
    position: absolute;
    left: 0; right: 0;
    top: 176px;
    text-align: center;
    font-size: 96px;
  }
</style>
</head>
<body>
  <section class="card card-front">
    <div class="wordmark">PIMLU</div>
    <p class="address">PO Box 7314<br>Kelbrook NSW 2790</p>
    <ul class="contact-list">
      <li>
        <svg viewBox="0 0 24 24" aria-hidden="true"><path d="M6.6 10.8a15.1 15.1 0 0 0 6.6 6.6l2.2-2.2c.3-.3.7-.4 1-.2 1.1.4 2.3.6 3.6.6.6 0 1 .4 1 1V20c0 .6-.4 1-1 1A17 17 0 0 1 3 4c0-.6.4-1 1-1h3.5c.6 0 1 .4 1 1 0 1.3.2 2.5.6 3.6.1.3 0 .7-.2 1z"/></svg>
        0400 318 592
      </li>
      <li>
        <svg viewBox="0 0 24 24" aria-hidden="true"><path d="M2 5h20v14H2z M4 7v.5l8 5 8-5V7l-8 5z" fill-rule="evenodd"/></svg>
        liam@pimlu.com
      </li>
      <li>
        <svg viewBox="0 0 24 24" aria-hidden="true"><path d="M12 2a10 10 0 1 0 0 20 10 10 0 0 0 0-20zm-1 17.9A8 8 0 0 1 4.1 10L9 15v1a2 2 0 0 0 2 2zm6.9-2.5A2 2 0 0 0 16 16h-1v-3a1 1 0 0 0-1-1H8v-2h2a1 1 0 0 0 1-1V7h2a2 2 0 0 0 2-2v-.4a8 8 0 0 1 2.9 12.8z"/></svg>
        www.pimlu.com
      </li>
    </ul>
    <div class="portrait" role="img" aria-label="Portrait photo of the agent"></div>
    <div class="agent">
      <p class="agent-name">Liam Carter</p>
      <p class="agent-title">Licenced Real Estate Agent</p>
    </div>
    <div class="rule-thin"></div>
    <div class="rule-band"></div>
  </section>

  <section class="card card-back">
    <div class="wordmark">PIMLU</div>
  </section>
</body>
</html>
```